Business Card Design for my Real Estate Investing Company

This is for a Real Estate Investing Company that will be serving the Las Vegas Valley. Id like the following slogan included: "Investing in Our Community" I have attached my logo. You will see the color tones I'm interested in..in my logo. I would like the card to be double-sided with a modern, professional look.
Target Market(s)
Homeowners, banks, real estate industry
Industry/Entity Type
Real Estate
Contact Information for Business Card
name: Dale Harwick
position: Managing Member
address: 4821 Corliss Pkwy ste 207-300
N. Harlow Flats, NV 89921
phone: (702) 555-0143
fax: (702) 555-0187
email: SummitRidgeEstate@hollowmail.test
web: SummitRidgeEstates.test
*At the bottom of the card I would like....
We buy houses for cash....no repairs, no commissions, no fees!
Logo Text
SUMMIT RIDGE ESTATES "Investing in Our Community"
Font styles to use
Other font styles liked:
- Lora
Requirements
Must have
- On the back of the card, i'd like to have my logo large and the following statements:
- Are you considering selling your home? Want a simple, hassle-free transaction? We can help! We buy houses for cash and can close quickly! No need to do any repairs, no realtor commissions, no closing costs.....and no headaches. Let us help you with your real estate needs...!
Nice to have
- multiple colors 2 two tone on front and back

```html
<!DOCTYPE html>
<html lang="en">
<head>
<meta charset="utf-8">
<title>Summit Ridge Estates – Business Card</title>
<link href="https://fonts.googleapis.com/css2?family=Lora:ital,wght@0,500;0,700;1,500&family=Open+Sans:wght@400;600&display=swap" rel="stylesheet">
<style>
  :root {
    --backdrop: #2e2e30;
    --card: #161617;
    --card-edge: #232325;
    --brand-blue: #1f6fc9;
    --ink-light: #ecedef;
    --ink-muted: #c9cbcf;
  }
  * { box-sizing: border-box; margin: 0; padding: 0; }
  html, body {
    width: 1200px; height: 900px; overflow: hidden;
    background: var(--backdrop);
  }
  .stage {
    position: relative; width: 1200px; height: 900px;
    display: flex; align-items: center; justify-content: center; gap: 40px;
  }
  .card {
    position: relative; width: 520px; height: 300px;
    background: var(--card);
    border: 1px solid var(--card-edge);
    border-radius: 22px;
    box-shadow: 0 14px 30px rgba(0,0,0,.45);
    color: var(--ink-light);
    font-family: "Open Sans", Arial, sans-serif;
    overflow: hidden;
  }

  /* Front */
  .front-brand {
    position: absolute; left: 34px; top: 150px;
    display: flex; align-items: center; gap: 10px;
  }
  .brand-square { width: 16px; height: 16px; background: var(--brand-blue); flex: none; }
  .brand-name {
    font-family: "Lora", Georgia, serif; font-weight: 700;
    color: var(--brand-blue); font-size: 17px; letter-spacing: .5px; line-height: 1.15;
  }
  .contact {
    position: absolute; left: 250px; top: 38px; width: 250px;
  }
  .contact-name {
    font-family: "Lora", Georgia, serif; font-weight: 700;
    color: var(--brand-blue); font-size: 19px; letter-spacing: .6px;
  }
  .contact-role { font-size: 13px; color: var(--ink-muted); margin-bottom: 14px; }
  .contact-address { font-size: 13px; line-height: 1.35; margin-bottom: 14px; }
  .contact-lines { list-style: none; font-size: 13px; line-height: 1.45; }
  .contact-lines li { display: flex; align-items: center; gap: 8px; white-space: nowrap; }
  .contact-lines svg { width: 11px; height: 11px; flex: none; fill: var(--brand-blue); }
  .tagline {
    position: absolute; left: 0; right: 0; bottom: 26px; text-align: center;
    font-family: "Lora", Georgia, serif; font-style: italic; font-weight: 500;
    color: var(--brand-blue); font-size: 16px;
  }

  /* Back */
  .back-brand {
    position: absolute; left: 0; right: 0; top: 44px; text-align: center;
  }
  .back-brand .brand-row { display: inline-flex; align-items: center; gap: 12px; }
  .back-brand .brand-square { width: 22px; height: 22px; }
  .back-brand .brand-name { font-size: 30px; letter-spacing: 1px; }
  .slogan {
    margin-top: 4px;
    font-family: "Lora", Georgia, serif; font-style: italic; font-weight: 500;
    font-size: 13px; letter-spacing: 3px; color: var(--ink-light);
  }
  .pitch {
    position: absolute; left: 48px; right: 48px; top: 140px;
    text-align: center; font-size: 13.5px; line-height: 1.45; color: var(--ink-light);
  }
</style>
</head>
<body>
<main class="stage">

  <section class="card card-front" aria-label="Business card front">
    <div class="front-brand">
      <span class="brand-square"></span>
      <span class="brand-name">SUMMIT RIDGE<br>ESTATES</span>
    </div>
    <div class="contact">
      <h1 class="contact-name">DALE HARWICK</h1>
      <p class="contact-role">Managing Member</p>
      <p class="contact-address">4821 Corliss Pkwy ste 207-300<br>N. Harlow Flats, NV 89921</p>
      <ul class="contact-lines">
        <li><svg viewBox="0 0 12 12"><path d="M2 1h2l1 3-1.3 1a6 6 0 0 0 3.3 3.3L8 7l3 1v2a1 1 0 0 1-1 1A9 9 0 0 1 1 2a1 1 0 0 1 1-1z"/></svg>(702) 555-0143</li>
        <li><svg viewBox="0 0 12 12"><rect x="3" y="1" width="6" height="3"/><rect x="1" y="5" width="10" height="5" rx="1"/></svg>(702) 555-0187</li>
        <li><svg viewBox="0 0 12 12"><path d="M1 3h10v6H1z M1 3l5 3.5L11 3" stroke="#161617" stroke-width=".8"/></svg>SummitRidgeEstate@hollowmail.test</li>
        <li><svg viewBox="0 0 12 12"><circle cx="6" cy="6" r="5"/></svg>SummitRidgeEstates.test</li>
      </ul>
    </div>
    <p class="tagline">We buy houses for cash....no repairs, no commissions, no fees!</p>
  </section>

  <section class="card card-back" aria-label="Business card back">
    <div class="back-brand">
      <div class="brand-row">
        <span class="brand-square"></span>
        <span class="brand-name">SUMMIT RIDGE ESTATES</span>
      </div>
      <p class="slogan">“Investing in Our Community”</p>
    </div>
    <p class="pitch">Are you considering selling your home? Want a simple, hassle-free transaction? We can help! We buy houses for cash and can close quickly! No need to do any repairs, no realtor commissions, no closing costs.....and no headaches. Let us help you with your real estate needs...!</p>
  </section>

</main>
</body>
</html>
```